Construction Company Cellar Crafters needs Business Card

I would like modern looking business card design. I am attaching logo of our company. Please include cell nr 302.418.7650 , email address cellarcrafters4u@examplemail.com, web : cellarcrafters4u.com, please also include wording: Specializing in finishing and remodeling basements. You can play with dark grey and orange colors or any ideas are welcome. Also include social media icons Friendloop and HouseGuidr.

```html
<!DOCTYPE html>
<html lang="en">
<head>
<meta charset="utf-8">
<title>Cellar Crafters – Business Card</title>
<link rel="stylesheet" href="https://fonts.googleapis.com/css2?family=Open+Sans:wght@400;600;700&display=swap">
<style>
  :root {
    --orange: #f05a28;
    --paper: #f4f2f1;
    --backdrop: #e6e3e1;
    --white: #ffffff;
    --ink: #2b2b2b;
    --faint: rgba(240, 90, 40, 0.22);
  }
  * { box-sizing: border-box; margin: 0; padding: 0; }
  html, body { width: 1200px; height: 900px; overflow: hidden; }
  body {
    position: relative;
    background: var(--backdrop);
    font-family: "Open Sans", Arial, sans-serif;
  }
  .card {
    position: absolute;
    width: 556px;
    height: 344px;
    background: var(--paper);
    box-shadow: 0 6px 18px rgba(0,0,0,0.12);
    overflow: hidden;
  }
  .card--front { left: 238px; top: 61px; }
  .card--back { left: 460px; top: 518px; height: 343px; }
  .card__top {
    height: 187px;
    display: flex;
    align-items: flex-end;
    justify-content: center;
    padding-bottom: 30px;
  }
  .card__band {
    position: absolute;
    left: 0; right: 0; top: 187px; bottom: 0;
    background: var(--orange);
    color: var(--white);
  }
  .brand-name {
    font-weight: 700;
    font-size: 40px;
    letter-spacing: 3px;
    text-transform: uppercase;
    color: var(--orange);
    line-height: 1;
  }
  .card--back .brand-name { color: var(--faint); }

  .holder {
    position: absolute;
    right: 350px;
    top: 58px;
    text-align: right;
  }
  .holder__name { font-weight: 600; font-size: 17px; line-height: 22px; }
  .holder__title { font-size: 14px; line-height: 20px; }

  .contacts {
    position: absolute;
    left: 230px;
    top: 50px;
    list-style: none;
    font-size: 14px;
    line-height: 20px;
  }
  .contacts li { display: flex; align-items: center; gap: 8px; }
  .contacts svg { width: 12px; height: 12px; fill: var(--white); flex: none; }

  .social {
    position: absolute;
    left: 0; right: 0; top: 44px;
    display: flex;
    justify-content: center;
    gap: 22px;
    font-size: 15px;
    font-weight: 600;
  }
  .social__item { display: flex; align-items: center; gap: 7px; }
  .social__mark { width: 18px; height: 18px; background: var(--white); border-radius: 2px; }
  .tagline {
    position: absolute;
    left: 0; right: 0; top: 109px;
    text-align: center;
    font-size: 14px;
    text-transform: uppercase;
  }
</style>
</head>
<body>
  <section class="card card--front">
    <div class="card__top"><span class="brand-name">Cellar Crafters</span></div>
    <div class="card__band">
      <div class="holder">
        <p class="holder__name">Daniel Brooks</p>
        <p class="holder__title">Managing Director</p>
      </div>
      <ul class="contacts">
        <li>
          <svg viewBox="0 0 24 24" aria-hidden="true"><path d="M6.6 10.8a15.1 15.1 0 0 0 6.6 6.6l2.2-2.2a1 1 0 0 1 1-.25 11.4 11.4 0 0 0 3.6.57 1 1 0 0 1 1 1V20a1 1 0 0 1-1 1A17 17 0 0 1 3 4a1 1 0 0 1 1-1h3.5a1 1 0 0 1 1 1c0 1.25.2 2.45.57 3.57a1 1 0 0 1-.25 1z"/></svg>
          302.418.7650
        </li>
        <li>
          <svg viewBox="0 0 24 24" aria-hidden="true"><path d="M2 5h20v14H2z M3 6l9 7 9-7" fill="none" stroke="#fff" stroke-width="2.5"/><path d="M2 5h20v3l-10 7L2 8z"/></svg>
          cellarcrafters4u@examplemail.com
        </li>
        <li>
          <svg viewBox="0 0 24 24" aria-hidden="true"><circle cx="12" cy="12" r="10"/><path d="M2 12h20M12 2c3 3 3 17 0 20M12 2c-3 3-3 17 0 20" stroke="#f05a28" stroke-width="1.5" fill="none"/></svg>
          cellarcrafters4u.com
        </li>
      </ul>
    </div>
  </section>

  <section class="card card--back">
    <div class="card__top"><span class="brand-name">Cellar Crafters</span></div>
    <div class="card__band">
      <div class="social">
        <span class="social__item"><span class="social__mark"></span>Friendloop</span>
        <span class="social__item"><span class="social__mark"></span>HouseGuidr</span>
      </div>
      <p class="tagline">Specializing in finishing and remodeling basements.</p>
    </div>
  </section>
</body>
</html>
```